Real Estate Business Card

On the front side I want to have my info, my brokerage info.
On the back side I want have my complany’s logo, website and Facebook link. I will provide all this once I select a design.

I would like to see Black background and gold text, Dark Blue and gold text and White and blue text designs

Font styles to use
Sans Serif
Script

```html
<!DOCTYPE html>
<html lang="en">
<head>
<meta charset="utf-8">
<title>Northgate Homes – Business Card</title>
<link rel="stylesheet" href="https://fonts.googleapis.com/css2?family=Cinzel:wght@500;600&family=Open+Sans:wght@400&display=swap">
<style>
  :root {
    --backdrop: #5c5c5c;
    --card-light: #f3f3f3;
    --card-navy: #12325a;
    --brand-blue: #1f4fa0;
    --text-grey: #3a3a3a;
    --gold: #f0c93a;
    --white: #ffffff;
    --rule-light: #6f87a6;
  }
  * { box-sizing: border-box; margin: 0; padding: 0; }
  html, body { width: 1200px; height: 900px; overflow: hidden; }
  body {
    background: var(--backdrop);
    position: relative;
    font-family: "Open Sans", sans-serif;
  }
  .card {
    position: absolute;
    top: 200px;
    width: 310px;
    height: 502px;
  }
  .card--front {
    left: 253px;
    background: var(--card-light);
    border-radius: 62px 0 62px 0;
  }
  .card--back {
    left: 627px;
    background: var(--card-navy);
    border-radius: 0 62px 0 62px;
  }
  .brand-name {
    position: absolute;
    left: 0;
    width: 100%;
    text-align: center;
    font-family: "Cinzel", serif;
    font-weight: 600;
    font-size: 30px;
    letter-spacing: 0.5px;
    line-height: 1;
  }
  .card--front .brand-name { top: 152px; color: var(--brand-blue); }
  .card--back .brand-name { top: 220px; color: var(--gold); }

  .contact {
    position: absolute;
    left: 33px;
    top: 284px;
    color: var(--text-grey);
  }
  .contact__name {
    font-family: "Cinzel", serif;
    font-weight: 600;
    font-size: 18.5px;
    color: var(--brand-blue);
    letter-spacing: 0.6px;
    line-height: 22px;
  }
  .contact__title { font-size: 14.5px; line-height: 20px; margin-bottom: 6px; }
  .contact__list { list-style: none; font-size: 14.5px; line-height: 18.3px; }
  .contact__list li { display: flex; align-items: center; gap: 5px; }
  .contact__list svg { width: 12px; height: 12px; fill: var(--brand-blue); flex: none; }
  .contact__address { font-size: 14.5px; line-height: 18px; margin-top: 11px; }

  .back__web, .back__social {
    position: absolute;
    left: 0;
    width: 100%;
    text-align: center;
    color: var(--white);
    font-size: 12.5px;
    letter-spacing: 0.4px;
    text-transform: uppercase;
  }
  .back__web { top: 309px; }
  .back__social { top: 429px; }
  .back__divider {
    position: absolute;
    top: 388px;
    left: 31px;
    width: 248px;
    height: 30px;
  }
</style>
</head>
<body>
  <section class="card card--front" aria-label="Business card front">
    <h1 class="brand-name">Northgate Homes</h1>
    <div class="contact">
      <p class="contact__name">Daniel Harper</p>
      <p class="contact__title">Managing Director</p>
      <ul class="contact__list">
        <li><svg viewBox="0 0 12 12"><path d="M1 4c0-2 3-3 5-3s5 1 5 3l-2 1-1-2H4L3 5zM2 6h8v4H2z"/></svg>044-123 456 789</li>
        <li><svg viewBox="0 0 12 12"><path d="M3 0h6v12H3zM4 1.5v7h4v-7zM5.5 9.5h1v1h-1z" fill-rule="evenodd"/></svg>044-123 456 789</li>
        <li><svg viewBox="0 0 12 12"><path d="M3 1h6v3H3zM1 4h10v5H9v2H3V9H1zM4 7v3h4V7z" fill-rule="evenodd"/></svg>044-123 456 789</li>
        <li><svg viewBox="0 0 12 12"><path d="M1 3h10v7H1zM1.5 3.5L6 7l4.5-3.5" /><path d="M1.8 3.6L6 6.8l4.2-3.2" fill="none" stroke="#f3f3f3" stroke-width="0.9"/></svg>hello@northgatehomes.com</li>
        <li><svg viewBox="0 0 12 12"><circle cx="6" cy="6" r="5.2"/><path d="M1 6h10M6 1c-2 2.5-2 7.5 0 10M6 1c2 2.5 2 7.5 0 10" fill="none" stroke="#f3f3f3" stroke-width="0.8"/></svg>www.northgatehomes.com</li>
      </ul>
      <p class="contact__address">12345, Address Goes Here<br>Country Name, 123456.</p>
    </div>
  </section>

  <section class="card card--back" aria-label="Business card back">
    <h2 class="brand-name">Northgate Homes</h2>
    <p class="back__web">www.northgatehomes.com</p>
    <svg class="back__divider" viewBox="0 0 248 30" aria-hidden="true">
      <line x1="0" y1="15" x2="100" y2="15" stroke="var(--rule-light)" stroke-width="1"/>
      <line x1="148" y1="15" x2="248" y2="15" stroke="var(--rule-light)" stroke-width="1"/>
      <circle cx="124" cy="15" r="15" fill="var(--white)"/>
    </svg>
    <p class="back__social">www.social.com/northgatehomes</p>
  </section>
</body>
</html>
```